Manual design

Hello,

I am looking for someone creative to help me design my Real Estate related manual. I am looking for something simple yet impressive. It would be designed around my logo and brand colors and I would also like it to have a local feel, perhaps with photos I could provide of my area/hometown. I am really shooting for an impressive company and branded look, while keeping it neat without too much going on.

I have the content that I would like to include, I am just struggling with the design of the manual in general.

I have attached a copy of my logo, my companys logo, and a publisher file of what I had previously done. Please do not think the design I previously used is something to work off of if you deem it better to use another feel. I am looking for originality, unless you can improve upon my old file. Any questions, please feel free to reach out to me.

The content in the provided brochure will remain the same, it is the design aspect I need help with. Thanks

Target Market(s)

My target market is home sellers aged 25-55, people usually selling their 1st or second home

Industry/Entity Type

Real Estate

Requirements
Must have
• -A simple to read design focused around my logo and colors
-A local sense
Should not have
• Drawings, only real photos

```html
<!DOCTYPE html>
<html lang="en">
<head>
<meta charset="utf-8">
<title>Educated Seller's Guide – Colin Marwood</title>
<link href="https://fonts.googleapis.com/css2?family=Jost:wght@300;400;500;600&display=swap" rel="stylesheet">
<style>
  :root {
    --navy: #0f2a5e;
    --navy-deep: #0b1f48;
    --ink: #111111;
    --ghost: #e6e6e6;
    --white: #ffffff;
    --muted: #c9d3e6;
    --line: #d9d9d9;
  }
  html, body { margin: 0; padding: 0; overflow: hidden; background: var(--white); }
  .spread {
    position: relative; width: 1200px; height: 848px; overflow: hidden;
    font-family: "Jost", "Century Gothic", sans-serif; color: var(--ink);
    background: var(--white);
  }

  /* Left cover page */
  .cover { position: absolute; left: 0; top: 0; width: 593px; height: 848px; }
  .cover-photo {
    position: absolute; inset: 0;
    background:
      linear-gradient(90deg, rgba(8,18,40,.55) 0%, rgba(8,18,40,0) 55%),
      linear-gradient(180deg,
        #1a2c5c 0%, #3a5f9c 14%, #6f93c8 26%, #b7c4d4 38%,
        #9aa7b6 48%, #5d6c80 58%, #3f5a4a 66%, #2c4b4c 74%,
        #1f3c40 86%, #173034 100%);
  }
  .quote {
    position: absolute; left: 32px; top: 538px; margin: 0;
    color: var(--white); font-weight: 300; font-size: 19.5px; line-height: 25px;
  }
  .quote cite { display: block; font-style: italic; font-weight: 400; }

  .agent-band {
    position: absolute; left: 0; top: 771px; width: 593px; height: 62px;
    background: var(--navy); color: var(--white);
  }
  .agent-site {
    position: absolute; left: 20px; top: 8px; width: 70px; text-align: center;
    font-size: 11px; font-weight: 500; color: var(--muted);
  }
  .agent-site .mark {
    display: block; width: 30px; height: 30px; margin: 0 auto 4px;
    background: var(--muted);
  }
  .agent-name {
    position: absolute; left: 108px; top: 2px; margin: 0;
    font-size: 35px; font-weight: 600; letter-spacing: .3px;
  }
  .agent-title {
    position: absolute; left: 109px; top: 42px; font-size: 12.5px; font-weight: 300; color: var(--muted);
  }
  .agent-contact {
    position: absolute; right: 14px; top: 17px; text-align: right;
    font-size: 14px; font-weight: 300; line-height: 22px; letter-spacing: .5px;
  }

  /* Right contents page */
  .contents { position: absolute; left: 593px; top: 0; width: 607px; height: 848px; }
  .ghost-title {
    position: absolute; left: 0; top: 40px; margin: 0;
    font-size: 86px; font-weight: 300; color: var(--ghost); white-space: nowrap;
  }
  .guide-title {
    position: absolute; left: 28px; top: 72px; margin: 0;
    font-size: 30px; font-weight: 400; color: var(--ink);
  }
  .wave-band {
    position: absolute; left: 0; top: 300px; width: 607px; height: 360px;
    background: radial-gradient(ellipse 70% 30% at 60% 40%, rgba(0,0,0,.05), rgba(0,0,0,0) 70%);
  }
  .toc-heading {
    position: absolute; left: 32px; top: 245px; margin: 0;
    font-size: 19px; font-weight: 600;
  }
  .toc {
    position: absolute; left: 32px; top: 281px; width: 535px;
    list-style: none; margin: 0; padding: 0;
    font-size: 18px; font-weight: 300; line-height: 25.2px;
  }
  .toc li { display: flex; justify-content: space-between; }

  .broker {
    position: absolute; right: 24px; top: 786px; text-align: center;
    color: var(--navy); font-weight: 600; font-size: 17px; line-height: 17px;
  }
</style>
</head>
<body>
<div class="spread">

  <section class="cover">
    <div class="cover-photo" role="img" aria-label="Photo of a waterfront city skyline with tall towers under a blue sky, a green park and a harbour with moored boats"></div>
    <blockquote class="quote">
      First comes thought;<br>
      then organization of that thought,<br>
      into ideas and plans;<br>
      then transformation of those plans into reality.<br>
      The beginning, as you will observe,<br>
      is in your imagination.
      <cite>-Elias Thorne</cite>
    </blockquote>

    <footer class="agent-band">
      <div class="agent-site"><span class="mark"></span>marwood.ca</div>
      <h2 class="agent-name">Colin Marwood</h2>
      <div class="agent-title">Multi-Award Winning Real Estate Professional</div>
      <div class="agent-contact">604-555-0182<br>homes@marwood.ca</div>
    </footer>
  </section>

  <section class="contents">
    <p class="ghost-title" aria-hidden="true">Seller's Guide</p>
    <h1 class="guide-title">Educated Seller's Guide</h1>
    <div class="wave-band" role="img" aria-label="Faint flowing line pattern decoration"></div>

    <h3 class="toc-heading">Table of Contents</h3>
    <ul class="toc">
      <li><span>Meet Colin Marwood</span><span>1</span></li>
      <li><span>About Harbourline Realty</span><span>2</span></li>
      <li><span>How to Qualify A Real Estate Professional</span><span>3</span></li>
      <li><span>How I Can Help You</span><span>4,5</span></li>
      <li><span>Where Do Buyers Come From 6</span><span>6</span></li>
      <li><span>Marketing Systems 7,8</span><span>7,8</span></li>
      <li><span>Intelligent Home Pricing 9</span><span>9</span></li>
      <li><span>Your Exclusive Entitlements 10</span><span>12</span></li>
      <li><span>Preparing Your Home for Sale 11</span><span>11</span></li>
      <li><span>Keys to Successful Showings 12</span><span>12</span></li>
      <li><span>Exclusive Easy Exit Guarantee 13</span><span>13</span></li>
      <li><span>A Few Words from Clients 14</span><span>14</span></li>
      <li><span>Forms to Prepare in Advance 15</span><span>15</span></li>
    </ul>

    <div class="broker">HARBOURLINE<br>REALTY</div>
  </section>

</div>
</body>
</html>
```